verdant terraces simple classy business card design

my name is colin barrow and I run a gardening business aimed at high class verdant terraces. the business name is verdant terraces and our logo was designed on pixel harbour .My clientel are anything from residential homes to businesses. I take pride in my work and know that I offer a service like no other in my area.
The business card will be used to represent my business and I want it to be not only rememberable, but simplistic and modern. Eye catching too. Of course I would like it relatable to gardening and appealing to the correct clientel - those being garden enthusiasts, prestigious homes and businesses that are after top of the line gardening services like no other on the market.
I am not a typical lawn mowing business so I don't want a typical card design that represents that. The gardens I work with are generally million dollar properties with owners who are very garden proud looking for upkeep and guidance from me along with sometimes whole new garden designs. I want the business cards to show to my clients that I take pride, as they do, in their garden. And I want them to know from my card that I am a professional, qualified horticulturist offering them a top of the line service for life. I want them to refer my business on. I want them to look at my business card and see class and professionalism in a modern unique bold way.
The card should be simple with the possibility of the logo on the front being embossed/debossed and my details on the back the card should have a organic garden feel it's very important to me that it is absolutely perfect
I am also very open to ideas and suggestions so look forward to seeing the designs. the business logo has been supplied with this project and I want the card to be double sided

Contact info is
Colin Barrow - Managing Director / Horticulturist
Phone : 0481 526 704
Email: colinbarrow@verdantterraces.example.au

Target Market(s)

high class gardens residential and commercial

Industry/Entity Type

Gardener

Contact Information for Business Card

Contact info is
Phone : 0481 526 704

PLEASE MAKE CARD DOUBLE SIDED

Requirements
Must have
• organic simple classy modern feel
• must flow with the current logo that has been supplied with this project
• Double sided
• Must explain in a simple way that I deal with high end gardens and I'm a qualified horticulturist
Nice to have
• embossed debossed logo
Should not have
• shouldn't be to busy or cheap looking

```html
<!DOCTYPE html>
<html lang="en">
<head>
<meta charset="utf-8">
<title>Verdant Terraces – Business Card</title>
<link href="https://fonts.googleapis.com/css2?family=Open+Sans:wght@400;600;700&display=swap" rel="stylesheet">
<style>
  :root {
    --leaf: #66a15a;
    --ink: #2a2a2a;
    --paper: #ffffff;
    --backdrop: #ecebe7;
    --text: #3a3a3a;
    --muted: #6b6b6b;
  }
  * { box-sizing: border-box; margin: 0; padding: 0; }
  html, body { width: 1200px; height: 900px; overflow: hidden; }
  body {
    background: var(--backdrop);
    font-family: "Open Sans", Arial, sans-serif;
    position: relative;
  }
  .card {
    position: absolute;
    left: 280px;
    width: 640px;
    height: 365px;
    overflow: hidden;
    box-shadow: 0 6px 18px rgba(0,0,0,0.12);
  }
  .card--front { top: 45px; background: var(--leaf); }
  .card--back { top: 470px; background: var(--paper); }

  .wordmark {
    position: absolute;
    display: flex;
    align-items: center;
    gap: 16px;
    font-weight: 600;
    text-transform: uppercase;
    letter-spacing: 0.12em;
    line-height: 1.05;
  }
  .wordmark__dot {
    width: 46px; height: 46px; border-radius: 50%;
    background: currentColor; flex: none;
  }
  .wordmark__name { font-size: 34px; }
  .card--front .wordmark { color: var(--ink); left: 50%; top: 50%; transform: translate(-50%, -50%); }
  .card--back .wordmark { color: var(--leaf); left: 360px; top: 148px; }
  .card--back .wordmark__name { font-size: 26px; }
  .card--back .wordmark__dot { width: 36px; height: 36px; }

  .card__shapes { position: absolute; inset: 0; }

  .holder { position: absolute; left: 100px; top: 28px; }
  .holder__name { color: var(--leaf); font-weight: 700; font-size: 19px; }
  .holder__role { color: var(--text); font-size: 13px; margin-top: 1px; }
  .holder__tagline { color: var(--muted); font-size: 12px; margin-top: 4px; }

  .contact {
    position: absolute; left: 34px; top: 166px;
    color: var(--text); font-size: 12.5px; line-height: 1.45;
    list-style: none;
  }
  .contact__address { margin-bottom: 6px; }
  .contact li { display: flex; align-items: center; gap: 8px; }
  .contact svg { width: 12px; height: 12px; flex: none; fill: var(--leaf); }
</style>
</head>
<body>

<section class="card card--front" aria-label="Card front">
  <div class="wordmark">
    <span class="wordmark__dot"></span>
    <span class="wordmark__name">Verdant<br>Terraces</span>
  </div>
</section>

<section class="card card--back" aria-label="Card back">
  <svg class="card__shapes" viewBox="0 0 640 365" aria-hidden="true">
    <polygon points="0,20 64,20 42,52 0,52" fill="var(--leaf)"/>
    <polygon points="68,20 90,20 68,52 46,52" fill="var(--ink)"/>
    <polygon points="0,268 300,268 288,292 0,292" fill="var(--leaf)"/>
    <polygon points="298,298 640,298 640,365 270,365" fill="var(--ink)"/>
  </svg>

  <div class="holder">
    <p class="holder__name">Colin Barrow</p>
    <p class="holder__role">Managing Director / Horticulturist</p>
    <p class="holder__tagline">Qualified care for high-end residential &amp; commercial gardens</p>
  </div>

  <ul class="contact">
    <li class="contact__address">12 Fernleigh Lane, Greenvale<br>VIC 3059.</li>
    <li>
      <svg viewBox="0 0 24 24"><path d="M6.6 10.8a15.1 15.1 0 0 0 6.6 6.6l2.2-2.2c.3-.3.7-.4 1-.2 1.1.4 2.3.6 3.6.6.6 0 1 .4 1 1V20c0 .6-.4 1-1 1A17 17 0 0 1 3 4c0-.6.4-1 1-1h3.5c.6 0 1 .4 1 1 0 1.3.2 2.5.6 3.6.1.3 0 .7-.2 1z"/></svg>
      0481 526 704
    </li>
    <li>
      <svg viewBox="0 0 24 24"><path d="M2 5h20v14H2z M2 5l10 8 10-8" /></svg>
      colinbarrow@verdantterraces.example.au
    </li>
    <li>
      <svg viewBox="0 0 24 24"><circle cx="12" cy="12" r="10"/></svg>
      www.verdantterraces.example.au
    </li>
  </ul>

  <div class="wordmark">
    <span class="wordmark__dot"></span>
    <span class="wordmark__name">Verdant<br>Terraces</span>
  </div>
</section>

</body>
</html>
```